Disability Magazine – Cover + Full Inside Layout

About the Publication

Our magazine is a quarterly, high‑impact publication that celebrates the lives, achievements, and everyday experiences of people with disabilities. It aims to inform, inspire, and advocate for accessibility, inclusion, and empowerment across all communities.

Target Audience

Adults (18‑65) with visible or invisible disabilities
Caregivers, family members, and allies
Professionals in health, education, policy, and design fields
Advocates and NGOs focused on accessibility

Project Goals

Visually compelling cover that instantly signals the magazine’s inclusive mission.
Consistent, readable interior layout for feature articles, interviews, photo essays, and resource guides.
Design that works both in print (A4, 300 dpi) and digitally (PDF/online flipbook).

```html
<!DOCTYPE html>
<html lang="en">
<head>
<meta charset="utf-8">
<title>Reach &amp; Rise – Issue 01 Layout</title>
<link rel="stylesheet" href="https://fonts.googleapis.com/css2?family=Montserrat:wght@300;400;500;600;700;800&family=Oswald:wght@300;400;500&family=Open+Sans:wght@400;600;700&display=swap">
<style>
:root{
  --orange:#f9a35f;
  --orange-deep:#f7964a;
  --board:#8a8a8a;
  --paper:#ffffff;
  --ink:#1c1c1c;
  --grey:#8c8c8c;
  --light-grey:#a9a9a9;
}
*{margin:0;padding:0;box-sizing:border-box}
html,body{width:1200px;height:857px;overflow:hidden;background:var(--board)}
.board{position:relative;width:1200px;height:857px}
.page{position:absolute;background:var(--paper);box-shadow:2px 3px 8px rgba(0,0,0,.35);overflow:hidden;font-family:"Open Sans",sans-serif;color:var(--ink)}
.abs{position:absolute}
.photo{position:absolute}

/* Cover */
.cover{left:62px;top:84px;width:486px;height:688px;background:#3a2a22}
.cover .photo{inset:0;background:
  radial-gradient(ellipse at 30% 30%,rgba(230,220,205,.7),transparent 45%),
  radial-gradient(ellipse at 60% 70%,rgba(170,110,80,.6),transparent 50%),
  linear-gradient(120deg,#bfb6a6 0%,#8a6a55 35%,#4a3228 60%,#2a1e1a 80%,#9aa6a4 100%)}
.cover-title{left:28px;top:88px;font-family:"Montserrat",sans-serif;font-weight:800;font-size:47px;color:var(--orange);letter-spacing:-1px;white-space:nowrap}
.cover-sub{right:26px;top:132px;font-family:"Montserrat",sans-serif;font-size:7.5px;letter-spacing:1.5px;color:#fff}
.cover-teasers{right:26px;top:180px;text-align:right;font-family:"Oswald",sans-serif;font-size:8.2px;letter-spacing:1.2px;line-height:10.2px;color:#fff}
.cover-teasers p{margin-bottom:10.5px}
.cover-headline{left:27px;top:364px;font-family:"Oswald",sans-serif;font-weight:400;font-size:45px;line-height:46.5px;color:#fff;letter-spacing:.6px;white-space:nowrap}
.cover-tagline{left:27px;top:609px;width:196px;font-family:"Montserrat",sans-serif;font-size:8.3px;line-height:10px;color:#fff;letter-spacing:.3px}
.edition-badge{left:329px;top:502px;width:128px;height:128px;border-radius:50%;background:var(--orange);color:#fff;text-align:center;padding-top:36px}
.edition-badge .label{font-family:"Oswald",sans-serif;font-size:15px;letter-spacing:2.5px;line-height:18px}
.edition-badge .issue{font-family:"Montserrat",sans-serif;font-size:8.5px;letter-spacing:1px;margin-top:6px}

/* Shared interior */
.running-head{right:6px;top:20px;font-family:"Montserrat",sans-serif;font-size:3px;letter-spacing:.3px;font-weight:700}
.running-head span{font-weight:400;color:var(--orange)}
.folio{font-family:"Montserrat",sans-serif;font-size:2.8px;letter-spacing:.4px;color:var(--grey);font-weight:600}

/* Contents */
.contents{left:626px;top:65px;width:235px;height:331px}
.contents .brand{left:10px;top:21px;font-family:"Montserrat",sans-serif;font-weight:600;font-size:6.6px;letter-spacing:.6px;color:var(--orange)}
.contents .heading{left:13px;top:30px;font-family:"Montserrat",sans-serif;font-weight:300;font-size:30px;line-height:34px;letter-spacing:6.3px;color:#8f8f8f;white-space:nowrap}
.contents-band{left:0;top:68px;width:235px;height:28px;background:var(--orange)}
.band-item{top:8px;font-family:"Open Sans",sans-serif;font-size:3.6px;line-height:5.6px;font-weight:700;color:#fff;letter-spacing:.3px}
.contents .photo{left:0;top:97px;width:134px;height:196px;background:linear-gradient(160deg,#6a6a5e 0%,#8a7a66 40%,#5e7592 70%,#d8d6d0 100%)}
.caption-card{left:22px;top:271px;width:90px;height:34px;background:#eeeeee;text-align:center;padding-top:4px;font-family:"Montserrat",sans-serif;color:var(--grey)}
.caption-card .num{font-size:3.6px}
.caption-card .title{font-size:4.3px;color:#555;margin:2px 0}
.caption-card .desc{font-size:3px;line-height:3.6px}
.toc{left:143px;top:103px;width:84px;font-family:"Open Sans",sans-serif}
.toc-entry{margin-bottom:6.6px;font-size:3.4px;line-height:4.5px}
.toc-entry .n{color:var(--grey)}
.toc-entry .t{font-weight:700}
.toc-entry .t span{color:var(--orange);font-weight:600}
.toc-entry .d{color:var(--light-grey)}
.contents .folio{right:10px;top:305px}

/* Breaking barriers */
.feature{left:917px;top:65px;width:235px;height:331px}
.feature-title{left:22px;top:28px;font-family:"Montserrat",sans-serif;font-weight:600;font-size:13.6px;line-height:14.4px;color:var(--orange);letter-spacing:.3px}
.feature-dek{left:22px;top:74px;width:200px;font-family:"Montserrat",sans-serif;font-size:3.8px;line-height:4.3px;color:var(--grey)}
.feature .photo{left:22px;top:94px;width:199px;height:104px;background:linear-gradient(100deg,#2c6b70 0%,#c9b9a6 30%,#b08a66 55%,#e8e4df 80%,#cfc8bf 100%)}
.pull-quote{left:167px;top:93px;width:47px;height:56px;background:var(--orange);padding:10px 5px;font-family:"Open Sans",sans-serif;font-size:6px;line-height:7.6px;color:#222;letter-spacing:.3px}
.feature-body{left:21px;top:208px;width:122px;font-family:"Open Sans",sans-serif;font-size:3.7px;line-height:5.6px;border-left:.8px solid var(--orange);padding-left:1px}
.section-head{left:20px;top:251px;font-family:"Montserrat",sans-serif;font-weight:700;font-size:9.6px;line-height:11.5px;color:var(--orange);letter-spacing:.4px}
.fast-facts{left:109px;top:252px;width:110px;font-family:"Open Sans",sans-serif}
.fast-facts h3{font-size:5.8px;font-weight:700;margin-bottom:4px}
.fast-facts ul{padding-left:7px;font-size:3.6px;line-height:5.5px}
.feature .folio{right:10px;top:305px}

/* Interview */
.interview{left:626px;top:460px;width:235px;height:331px;background:var(--orange)}
.interview .running-head{left:9px;right:auto;color:var(--ink)}
.interview .running-head span{color:#fff}
.interview-title{left:16px;top:54px;font-family:"Montserrat",sans-serif;font-weight:700;font-size:19.5px;line-height:20.8px;color:#fff;letter-spacing:.5px}
.qa-card{left:16px;top:176px;width:89px;height:125px;background:#fff;padding:10px 7px}
.qa-card h3{font-family:"Montserrat",sans-serif;font-weight:700;font-size:4.6px;letter-spacing:.4px;margin-bottom:3px}
.qa-card p{font-family:"Open Sans",sans-serif;font-size:2.8px;line-height:4.1px;color:#555}
.qa-card .q{font-family:"Montserrat",sans-serif;font-weight:700;font-size:3.2px;line-height:4.4px;color:var(--ink);margin-top:12px}
.qa-card .r{font-size:2.8px;color:#777}
.interview .photo{left:105px;top:176px;width:114px;height:125px;background:linear-gradient(150deg,#d9e2d2 0%,#a8b98e 40%,#e8cbb6 60%,#5f89ad 100%)}
.interview .pull-quote{left:172px;top:138px;width:47px;height:56px;background:#fff;color:var(--orange);padding:11px 6px;font-size:5.8px;line-height:7.6px}
.interview .folio{left:15px;top:307px;color:var(--ink)}

/* Photo essay */
.essay{left:917px;top:460px;width:235px;height:331px}
.essay-frame{left:22px;top:34px;width:157px;height:64px;border:2px solid var(--ink);padding:15px 6px 0 11px}
.essay-frame h2{font-family:"Montserrat",sans-serif;font-weight:600;font-size:9px;line-height:10px;color:var(--orange);letter-spacing:0;white-space:nowrap}
.essay-intro{left:22px;top:116px;width:65px;font-family:"Open Sans",sans-serif;font-size:3.7px;line-height:5.6px}
.essay .photo{left:92px;top:115px;width:143px;height:187px;background:linear-gradient(170deg,#7fa36b 0%,#c9b8a0 35%,#3f6e62 60%,#2f3a44 100%)}
.essay-credit{left:22px;top:269px;width:66px;font-family:"Open Sans",sans-serif;font-size:3.6px;line-height:4.9px}
.essay-credit b{font-weight:700}
.essay .folio{right:10px;top:305px}
</style>
</head>
<body>
<main class="board">

  <section class="page cover">
    <div class="photo" role="img" aria-label="Photo of a smiling woman in a headscarf leaning on a café table, talking with a friend"></div>
    <h1 class="abs cover-title">REACH &amp; RISE</h1>
    <p class="abs cover-sub">THE MAGAZINE</p>
    <div class="abs cover-teasers">
      <p>INSIDE: 6 INNOVATORS<br>REIMAGINING ACCESSIBILITY</p>
      <p>LIFE &amp; STYLE: FASHION THAT<br>FITS EVERY BODY</p>
      <p>TECH SPOTLIGHT: TOOLS<br>TRANSFORMING DAILY<br>LIVING</p>
      <p>COMMUNITY: EMPOWERING<br>SUPPORT NETWORKS</p>
    </div>
    <h2 class="abs cover-headline">REDEFINING<br>STRENGTH:<br>REAL STORIES.<br>REAL VOICES.<br>REAL CHANGE.</h2>
    <p class="abs cover-tagline">Celebrating the achievements, creativity, and resilience of people with disabilities worldwide.</p>
    <div class="abs edition-badge">
      <div class="label">QUARTERLY<br>EDITION</div>
      <div class="issue">ISSUE 01 · 2025</div>
    </div>
  </section>

  <section class="page contents">
    <p class="abs brand">REACH &amp; RISE</p>
    <h2 class="abs heading">CONTENTS</h2>
    <div class="abs contents-band">
      <p class="abs band-item" style="left:13px">08<br>Redefining Strength</p>
      <p class="abs band-item" style="left:93px">12<br>EXCERPT: Letters From<br>the Ledge</p>
      <p class="abs band-item" style="left:166px">9<br>AUTHOR SPOTLIGHT:<br>Helen Marsh</p>
    </div>
    <div class="photo" role="img" aria-label="Photo of a woman with windswept hair seated at a vintage typewriter"></div>
    <div class="abs caption-card">
      <p class="num">20</p>
      <p class="title">8 Young Emerging Writers</p>
      <p class="desc">Get to know eight twenty-something<br>writers who will capture our literary hearts</p>
    </div>
    <div class="abs toc">
      <div class="toc-entry"><div class="n">14</div><div class="t">Breaking Barriers</div><div class="d">How inclusive design is reshaping the future of accessibility — from product design to public spaces.</div></div>
      <div class="toc-entry"><div class="n">40</div><div class="t">Everyday Brilliance</div><div class="d">A photo essay capturing candid moments of creativity, confidence, and expression.</div></div>
      <div class="toc-entry"><div class="n">43</div><div class="t">In Conversation With: Nora Castell</div><div class="d">Artist and advocate pushing new boundaries in digital accessibility.</div></div>
      <div class="toc-entry"><div class="n">52</div><div class="t">Voices of Change<span>Breaking Barriers</span></div><div class="d">Three leaders share their experiences championing inclusion in education, tech, and policy.</div></div>
      <div class="toc-entry"><div class="n">44</div><div class="t">Fashion That Fits Every Body</div><div class="d">Adaptive clothing brands rewriting the rules.</div></div>
      <div class="toc-entry"><div class="n">56</div><div class="t">Accessibility Resources You Should Know</div><div class="d">A curated list of services, rights, and tools.</div></div>
      <div class="toc-entry"><div class="n">48</div><div class="t">Your Rights: A Quick Overview</div><div class="d">Understanding disability laws, accommodations, and advocacy.</div></div>
    </div>
    <p class="abs folio">REACH &amp; RISE MAGAZINE &nbsp;| &nbsp;2</p>
  </section>

  <section class="page feature">
    <p class="abs running-head">REACH &amp; RISE <span>FEATURE</span></p>
    <h2 class="abs feature-title">BREAKING BARRIERS:<br>HOW INCLUSIVE DESIGN IS<br>RESHAPING THE FUTURE</h2>
    <p class="abs feature-dek">A deep dive into the designers, creators, and everyday advocates pushing accessibility into mainstream culture.</p>
    <div class="photo" role="img" aria-label="Photo of a hand in a teal sleeve holding a latte beside an open book"></div>
    <blockquote class="abs pull-quote">“Accessibility is not an add-on. It’s a human right.”</blockquote>
    <p class="abs feature-body">Inclusive design is no longer a niche practice—it’s becoming a global standard. From public spaces to digital platforms, accessibility is shaping the way we think about innovation. This feature explores the individuals leading the movement, their challenges, and the breakthroughs that redefine possibilities for all.</p>
    <h3 class="abs section-head">THE<br>MOVEMENT<br>GAINING<br>MOMENTUM</h3>
    <div class="abs fast-facts">
      <h3>Fast Facts</h3>
      <ul>
        <li>1.3 billion people worldwide live with a disability</li>
        <li>Accessibility increases usability for everyone</li>
        <li>Inclusive products lead to higher customer satisfaction</li>
      </ul>
    </div>
    <p class="abs folio">REACH &amp; RISE MAGAZINE &nbsp;| &nbsp;8</p>
  </section>

  <section class="page interview">
    <p class="abs running-head">REACH &amp; RISE <span>FEATURE</span></p>
    <h2 class="abs interview-title">IN<br>CONVERSATION<br>WITH:<br>NORA<br>CASTELL</h2>
    <div class="abs qa-card">
      <h3>Q&amp;A: NORA CASTELL</h3>
      <p>Nora Castell has spent the last decade breaking barriers through her art and activism. In this exclusive interview, she shares her journey, her vision, and her hopes for a more inclusive future.</p>
      <p class="q">WHAT SPARKED YOUR PASSION FOR ACCESSIBILITY ADVOCACY?</p>
      <p class="r">(Insert interview response)</p>
      <p class="q">WHAT CHANGES DO YOU HOPE TO SEE IN THE NEXT FIVE YEARS?</p>
      <p class="r">(Insert interview response)</p>
    </div>
    <div class="photo" role="img" aria-label="Photo of a smiling young woman writing in a notebook outdoors"></div>
    <blockquote class="abs pull-quote">“Representation isn’t optional—it’s essential.”</blockquote>
    <p class="abs folio">9 &nbsp;| &nbsp;REACH &amp; RISE MAGAZINE</p>
  </section>

  <section class="page essay">
    <p class="abs running-head">REACH &amp; RISE <span>FEATURE</span></p>
    <div class="abs essay-frame"><h2>EVERYDAY BRILLIANCE:<br>PORTRAITS OF STRENGTH<br>&amp; EXPRESSION</h2></div>
    <p class="abs essay-intro">A visual journey highlighting the beauty, confidence, and individuality of people living with visible and invisible disabilities.</p>
    <div class="photo" role="img" aria-label="Photo of a group of friends outdoors in a park, one seated in a wheelchair"></div>
    <div class="abs essay-credit">
      <p><b>Caption:</b><br>(Describe the person, moment, or story)</p>
      <p style="margin-top:5px"><b>Photo Credit:</b><br>(Photographer Name)</p>
    </div>
    <p class="abs folio">REACH &amp; RISE MAGAZINE &nbsp;| &nbsp;8</p>
  </section>

</main>
</body>
</html>
```